BrightHarbor logo and website profile

BrightHarbor is a newly started business angel network investing in entrepreneurs and start-ups. We need a smart looking logo and website design (based on Wordpress).
The aim of the site is to attract 2 customer segments;
1) Entrepreneurs and start-ups looking for investors
2) Investors/ business angels looking to become part of a larger network of investors for better access to investments
A successful conversion on the website would be for the entrepreneur or investor sending us an e-mail to submit their investment proposal, inquire about our services or ask to join the network of investors.
The website should focus on presenting Bright Harbor and our offerings towards the 2 customer segments. This is NOT a platform like e.g. fundly.example.
Sites we like;
http://demo.quilvex.example/themes/orchid/agency/
http://www.trellisadvisory.example (it's a bit bleak - needs a little more color)
Hi all,
Target Market(s)
Two target markets; 1) entrepreneurs looking for investors 2) business angels looking for investment opportunities
Industry/Entity Type
Investment
Requirements
Must have
- The keywords we want associated with our brand are;
Innovation – Integrity – Knowledgeable – Growth – Entrepreneurship
Logodesign (symbol and smart presentation of the company name - bright harbor, both with and without .com)
Wordpress design, pages we need:
- landing page with clear CTA for entrepreneurs and clear CTA for investors
- Portfolio overview of investments made
- General page for our approach, services etc
- Contact us page
- Favicon
- News
- Header/footer information
Other functionality we need;
- Social media integration
The design must support mobile and iPads as well.
We like: less is more :)

```html
<!DOCTYPE html>
<html lang="en">
<head>
<meta charset="utf-8">
<title>Bright Harbor</title>
<link rel="stylesheet" href="https://fonts.googleapis.com/css2?family=Oswald:wght@400;500&family=Ubuntu:ital@1&family=PT+Sans&display=swap">
<style>
  :root {
    --ink: #3a3a3a;
    --muted: #8a8a8a;
    --body: #5a5a5a;
    --black: #000000;
    --white: #ffffff;
    --page: #ebebeb;
    --red: #e3101c;
    --frame: #d9d9d9;
    --social-panel: #d3d3d3;
    --footer-base: #cccccc;
  }
  * { margin: 0; padding: 0; box-sizing: border-box; }
  html, body { width: 1126px; height: 1200px; overflow: hidden; }
  body { background: var(--page); font-family: Arial, Helvetica, sans-serif; position: relative; }

  .site-header { position: absolute; left: 0; top: 0; width: 1126px; height: 80px; background: var(--white); }
  .brand { position: absolute; left: 14px; top: 19px; display: flex; align-items: center; gap: 10px;
    font-family: "Oswald", sans-serif; font-weight: 500; font-size: 31px; line-height: 38px; color: var(--ink); letter-spacing: 0.5px; }
  .brand-mark { width: 18px; height: 18px; background: var(--red); }
  .header-contact { position: absolute; right: 10px; top: 12px; text-align: right; font-family: "Oswald", sans-serif; font-weight: 500; }
  .header-contact .label { font-size: 18px; line-height: 22px; color: var(--ink); }
  .header-contact .phone { font-size: 31px; line-height: 36px; color: #6e6e6e; }

  .main-nav { position: absolute; left: 0; top: 80px; width: 1126px; height: 65px; background: var(--black); }
  .main-nav a { position: absolute; top: 19px; font-family: "Ubuntu", sans-serif; font-style: italic; font-size: 17px; color: var(--white); text-decoration: none; }

  .hero { position: absolute; left: 0; top: 131px; width: 1126px; height: 484px; }

  .intro { position: absolute; top: 694px; width: 440px; }
  .intro h2 { font-family: "Oswald", sans-serif; font-weight: 500; font-size: 29px; line-height: 36px; color: var(--ink); letter-spacing: -1px; }
  .intro .tagline { font-family: "Oswald", sans-serif; font-size: 16px; line-height: 18px; color: var(--muted); text-align: right; letter-spacing: -0.3px; }
  .intro p { margin-top: 30px; font-size: 14px; line-height: 16.5px; color: var(--body); width: 425px; }
  .intro .cta { position: absolute; display: flex; align-items: center; gap: 12px; font-size: 13.5px; line-height: 15px; color: var(--black); text-decoration: none; }
  .intro .cta svg { flex: none; }
  .intro-investors { left: 36px; }
  .intro-investors p { margin-left: -7px; }
  .intro-investors .tagline { width: 402px; }
  .intro-investors .cta { top: 168px; left: -20px; }
  .intro-founders { left: 532px; }
  .intro-founders .tagline { width: 418px; }
  .intro-founders .cta { top: 168px; left: 4px; }

  .social-rail { position: absolute; left: 1021px; top: 654px; width: 80px; height: 341px; background: var(--social-panel); border-radius: 6px; list-style: none; }
  .social-rail li { position: absolute; left: 15px; width: 49px; height: 49px; border-radius: 10px;
    background: linear-gradient(#a8a8a8, #6e6e6e); box-shadow: inset 0 1px 0 rgba(255,255,255,.5);
    display: flex; align-items: center; justify-content: center;
    font-size: 11px; font-weight: bold; color: var(--white); letter-spacing: 0.2px; }

  .site-footer { position: absolute; left: 0; top: 1101px; width: 1126px; height: 46px; background: var(--black);
    display: flex; justify-content: center; align-items: center; gap: 12px; }
  .site-footer a { color: var(--white); text-decoration: none; font-size: 15px; }
  .site-footer .sep { color: #aaa; font-size: 12px; }
  .copyright { position: absolute; left: 0; top: 1147px; width: 1126px; height: 53px; background: var(--footer-base);
    text-align: center; font-family: "PT Sans", sans-serif; font-size: 13px; line-height: 50px; color: var(--black); }
</style>
</head>
<body>
  <header class="site-header">
    <div class="brand"><span class="brand-mark"></span>BRIGHT HARBOR</div>
    <div class="header-contact">
      <div class="label">CONTACT</div>
      <div class="phone">02-555-01234</div>
    </div>
  </header>

  <nav class="main-nav">
    <a href="#" style="left:193px">HOME</a>
    <a href="#" style="left:284px">PORTFOLIO</a>
    <a href="#" style="left:411px">APPROACH AND SERVICES</a>
    <a href="#" style="left:640px">NEWS</a>
    <a href="#" style="left:730px">CONTACT US</a>
  </nav>

  <svg class="hero" viewBox="0 131 1126 484" xmlns="http://www.w3.org/2000/svg">
    <defs>
      <linearGradient id="heroBackdrop" x1="0" y1="0" x2="0" y2="1">
        <stop offset="0" stop-color="#a2a2a2"/>
        <stop offset="0.66" stop-color="#6f6f6f"/>
        <stop offset="0.67" stop-color="#e3101c"/>
        <stop offset="1" stop-color="#b50d17"/>
      </linearGradient>
      <linearGradient id="investorSky" x1="0" y1="0" x2="1" y2="0.3">
        <stop offset="0" stop-color="#4aa7dd"/>
        <stop offset="0.6" stop-color="#7cc4ea"/>
        <stop offset="0.85" stop-color="#eef4f8"/>
        <stop offset="1" stop-color="#ffffff"/>
      </linearGradient>
      <linearGradient id="investorFade" x1="0" y1="0" x2="0" y2="1">
        <stop offset="0.4" stop-color="#1c2a48" stop-opacity="0"/>
        <stop offset="0.75" stop-color="#1c2a48" stop-opacity="0.85"/>
        <stop offset="1" stop-color="#141d34"/>
      </linearGradient>
      <linearGradient id="founderLight" x1="0" y1="0" x2="1" y2="0">
        <stop offset="0" stop-color="#d8d6d8"/>
        <stop offset="0.5" stop-color="#b9b6b9"/>
        <stop offset="1" stop-color="#f2f2f2"/>
      </linearGradient>
      <radialGradient id="founderSuit" cx="0.65" cy="0.8" r="0.55">
        <stop offset="0" stop-color="#1e1e22"/>
        <stop offset="0.7" stop-color="#2c2c30" stop-opacity="0.8"/>
        <stop offset="1" stop-color="#2c2c30" stop-opacity="0"/>
      </radialGradient>
    </defs>
    <rect x="0" y="145" width="1126" height="443" fill="url(#heroBackdrop)" role="img" aria-label="Steel and glass architecture backdrop with a red band"/>
    <rect x="0" y="586" width="1126" height="3" fill="#111"/>

    <polygon points="184,131 630,131 494,615 44,615" fill="var(--frame)"/>
    <g role="img" aria-label="Photo of a surprised investor holding a blue umbrella under falling banknotes">
      <polygon points="193,145 611,145 480,598 35,598" fill="url(#investorSky)"/>
      <polygon points="193,145 611,145 480,598 35,598" fill="url(#investorFade)"/>
    </g>

    <polygon points="664,131 1112,131 969,615 525,615" fill="var(--frame)"/>
    <g role="img" aria-label="Photo of an entrepreneur in a dark suit on a phone call">
      <polygon points="678,145 1094,145 949,598 545,598" fill="url(#founderLight)"/>
      <polygon points="678,145 1094,145 949,598 545,598" fill="url(#founderSuit)"/>
    </g>
  </svg>

  <section class="intro intro-investors">
    <h2>INVESTORS / BUSINESS ANGELS</h2>
    <div class="tagline">looking for better access to investments</div>
    <p>Are you wondering where to invest your money and looking for a successfull ROI? You just came to the right place, we can help you decide and find a good business investment the you desire.</p>
    <a class="cta" href="#">
      <svg width="32" height="32" viewBox="0 0 32 32" aria-hidden="true"><rect x="4" y="9" width="24" height="17" rx="2" fill="#cfcfcf" stroke="#999"/><polyline points="4,10 16,19 28,10" fill="none" stroke="#888" stroke-width="1.5"/></svg>
      <span>contact us and get a business proposal or<br>submit invsestment proposal</span>
    </a>
  </section>

  <section class="intro intro-founders">
    <h2>ENTREPRENEURS AND STARTUPS</h2>
    <div class="tagline">looking for investors</div>
    <p>Have a business in mind but don't have enought funds to continue with the venture? This is the right place to take your business into a higher next and look for investors to help you achive the business of your dreams.</p>
    <a class="cta" href="#">
      <svg width="32" height="32" viewBox="0 0 32 32" aria-hidden="true"><rect x="4" y="9" width="24" height="17" rx="2" fill="#cfcfcf" stroke="#999"/><polyline points="4,10 16,19 28,10" fill="none" stroke="#888" stroke-width="1.5"/></svg>
      <span>contact us and submit your business proposal</span>
    </a>
  </section>

  <ul class="social-rail" aria-label="Social links">
    <li style="top:14px">Like</li>
    <li style="top:78px">Follow</li>
    <li style="top:142px">Connect</li>
    <li style="top:208px">Watch</li>
    <li style="top:276px">Feed</li>
  </ul>

  <footer class="site-footer">
    <a href="#">HOME</a><span class="sep">·</span>
    <a href="#">PORTFOLIO</a><span class="sep">·</span>
    <a href="#">APPROACH AND SERVICES</a><span class="sep">·</span>
    <a href="#">NEWS</a><span class="sep">·</span>
    <a href="#">CONTACT US</a>
  </footer>
  <div class="copyright">© Copyright 2013 BRIGHT HARBOR All Rights Reserved.</div>
</body>
</html>
```